Red Mesa Greenworks Summit needs a marketing flyer

We need a full page graphic for our upcoming Forum that can also be converted into a website "header" for social media, etc.: "Red Mesa Greenworks Summit - Shaping Change Across the Made Landscape"

INTRODUCTION:
During the first week of August 2022, Q-VarDT is presenting the Red Mesa Greenworks Summit - Shaping Change Across the Made Landscape.

One of the most exciting aspects of this conference will be the bringing together of multiple organizations including for-profits and nonprofits, K-12’s and higher education, cities and counties and other governmental agencies, as well as architects, engineers, and contractors to collaboratively present and discuss issues and ideas related to sustainability, with a Texas focus.

This event will be a catalyst for public and private project owners to holistically gather information and momentum as we bring the resources and vision needed to achieve the goal of zero carbon emissions from the built environment by 2040, and address water, green space and the natural environment, transportation, equity, and funding, among other topics.

```html
<!DOCTYPE html>
<html lang="en">
<head>
<meta charset="utf-8">
<title>Red Mesa Greenworks Summit – Flyer</title>
<link href="https://fonts.googleapis.com/css2?family=Poppins:wght@300;400;500;600;700;800&display=swap" rel="stylesheet">
<style>
  :root{
    --blue:#1f3fa8;
    --blue-deep:#14287a;
    --green:#8cc63f;
    --green-dark:#6fae2a;
    --charcoal:#4d4f53;
    --ink:#2b2c30;
    --text:#55585e;
    --panel:#e4e5e8;
    --white:#ffffff;
  }
  *{margin:0;padding:0;box-sizing:border-box}
  html,body{width:750px;height:1200px;overflow:hidden;background:#d9dadc}
  body{font-family:"Poppins",sans-serif;color:var(--text)}
  .flyer{position:relative;width:750px;height:1200px;background:var(--white);overflow:hidden}
  .backdrop{position:absolute;inset:0;width:750px;height:1200px}
  .abs{position:absolute}

  .brand{left:0;right:0;top:66px;display:flex;justify-content:center;align-items:center;gap:12px}
  .brand-dot{width:50px;height:50px;border-radius:50%;background:var(--blue)}
  .brand-name{font-size:34px;font-weight:500;color:var(--charcoal);letter-spacing:.5px}

  .title{left:0;right:0;text-align:center;color:var(--white);font-weight:700;line-height:1}
  .title-main{top:244px;font-size:74px;letter-spacing:-1px}
  .title-main span{color:var(--green)}
  .title-sub{top:326px;font-size:39px;letter-spacing:-.3px}
  .title-rule{left:354px;top:380px;width:42px;height:3px;background:var(--green)}

  .tagline{left:0;right:0;top:476px;text-align:center;color:var(--white);font-weight:700;font-size:20px;line-height:29px}

  .when{left:60px;top:622px}
  .when-lead{font-size:17px;font-weight:500;color:var(--charcoal)}
  .date-pill{display:flex;margin-top:8px;width:192px;height:36px;border-radius:18px;overflow:hidden;font-size:19px;font-weight:600;color:var(--white)}
  .date-month{flex:1;background:var(--charcoal);display:flex;align-items:center;justify-content:center}
  .date-year{flex:1;background:var(--green);display:flex;align-items:center;justify-content:center;border-radius:18px 0 0 18px;margin-left:-10px}
  .divider-v{width:1px;background:#d3d4d7}
  .intro-div{left:270px;top:622px;height:70px}
  .intro{left:296px;top:620px;width:410px;font-size:17px;line-height:22px;color:var(--text)}
  .intro b{color:var(--ink);font-weight:600}
  .intro strong{color:var(--blue);font-weight:600}

  .lead{left:60px;top:734px;width:640px;font-size:14.5px;line-height:19px;font-weight:400}
  .lead-rule{left:60px;top:788px;width:44px;height:3px;background:var(--green)}

  .orgs{left:60px;top:812px;width:250px;list-style:none}
  .orgs::before{content:"";position:absolute;left:7px;top:12px;bottom:14px;border-left:1px dotted #9aa0b3}
  .orgs li{position:relative;padding-left:24px;font-size:14.5px;font-weight:500;line-height:18px;color:var(--charcoal);margin-bottom:16px}
  .orgs li svg{position:absolute;left:0;top:2px;width:14px;height:14px}
  .list-div{left:327px;top:815px;height:280px}

  .catalyst{left:358px;top:814px;width:333px;height:284px;background:var(--panel);border-radius:14px;box-shadow:0 3px 0 #cfd0d3}
  .catalyst-head{position:absolute;left:26px;top:24px;width:280px;height:38px;background:var(--white);border-radius:19px;display:flex;align-items:center;padding-left:0}
  .catalyst-dot{width:38px;height:38px;border-radius:50%;background:var(--blue);margin-right:20px}
  .catalyst-title{font-size:14px;font-weight:400;color:var(--ink)}
  .catalyst-title span{color:var(--green-dark);font-weight:600}
  .catalyst-body{position:absolute;left:28px;top:100px;width:278px;font-size:12.5px;line-height:17px;text-align:justify;color:var(--text)}

  .contact{top:1146px;font-size:12.5px;font-weight:500;color:var(--ink);display:flex;align-items:center;gap:5px}
  .contact svg{width:11px;height:11px}
  .phone{left:60px}
  .email{left:182px}
  .web{left:404px;top:1140px;font-size:19px;font-weight:700;color:var(--ink);letter-spacing:.3px}
  .web span{color:var(--green-dark)}
</style>
</head>
<body>
<main class="flyer">
  <svg class="backdrop" viewBox="0 0 750 1200" aria-hidden="false">
    <defs>
      <linearGradient id="blueBand" x1="0" y1="0" x2="1" y2="0">
        <stop offset="0" stop-color="#2a4fc4"/>
        <stop offset="1" stop-color="#163192"/>
      </linearGradient>
      <radialGradient id="photoTone" cx="0.5" cy="0.55" r="0.7">
        <stop offset="0" stop-color="#6a6c70"/>
        <stop offset="1" stop-color="#48494d"/>
      </radialGradient>
      <linearGradient id="greenArc" x1="0" y1="0" x2="0" y2="1">
        <stop offset="0" stop-color="#9bd14a"/>
        <stop offset="1" stop-color="#79b530"/>
      </linearGradient>
    </defs>
    <rect width="750" height="1200" fill="#ffffff"/>
    <path role="img" aria-label="Black and white photo of hands cradling a young seedling in soil with faint eco icons"
          d="M0 60 H750 V545 Q375 585 0 545 Z" fill="url(#photoTone)"/>
    <path d="M0 0 H750 V110 C620 45 450 30 375 30 C250 30 120 50 0 110 Z" fill="url(#blueBand)"/>
    <path d="M0 64 C140 40 260 34 375 34 C500 34 620 45 750 70 V84 C600 170 470 172 375 172 C270 172 130 160 0 84 Z" fill="#ffffff"/>
    <path d="M140 548 C210 470 300 444 375 444 C450 444 540 470 610 548 Q500 565 375 565 Q250 565 140 548 Z" fill="url(#greenArc)"/>
    <path d="M0 545 Q375 585 750 545 V560 Q375 600 0 560 Z" fill="#ffffff"/>
  </svg>

  <header class="abs brand">
    <span class="brand-dot"></span>
    <span class="brand-name">Q-VarDT</span>
  </header>

  <h1 class="abs title title-main">RED MESA <span>GREEN</span></h1>
  <h2 class="abs title title-sub">WORKS SUMMIT</h2>
  <div class="abs title-rule"></div>

  <p class="abs tagline">Shaping Change Across the<br>Made Landscape</p>

  <section class="abs when">
    <p class="when-lead">During the first week of</p>
    <div class="date-pill"><span class="date-month">AUGUST</span><span class="date-year">2022</span></div>
  </section>
  <div class="abs divider-v intro-div"></div>
  <p class="abs intro"><b>Q-VarDT is presenting the Red Mesa</b><br><strong>Greenworks Summit</strong> - Shaping Change Across<br>the Made Landscape.</p>

  <p class="abs lead">One of the most exciting aspects of this conference will be the bringing together of multiple organizations including</p>
  <div class="abs lead-rule"></div>

  <ul class="abs orgs">
    <li><svg viewBox="0 0 14 14"><circle cx="7" cy="7" r="7" fill="#1f3fa8"/><path d="M3.8 7.2l2.2 2.1 4.2-4.4" stroke="#fff" stroke-width="1.6" fill="none"/></svg>Profits and nonprofits</li>
    <li><svg viewBox="0 0 14 14"><circle cx="7" cy="7" r="7" fill="#1f3fa8"/><path d="M3.8 7.2l2.2 2.1 4.2-4.4" stroke="#fff" stroke-width="1.6" fill="none"/></svg>K-12’s and higher education</li>
    <li><svg viewBox="0 0 14 14"><circle cx="7" cy="7" r="7" fill="#1f3fa8"/><path d="M3.8 7.2l2.2 2.1 4.2-4.4" stroke="#fff" stroke-width="1.6" fill="none"/></svg>Cities and counties and other governmental agencies</li>
    <li><svg viewBox="0 0 14 14"><circle cx="7" cy="7" r="7" fill="#1f3fa8"/><path d="M3.8 7.2l2.2 2.1 4.2-4.4" stroke="#fff" stroke-width="1.6" fill="none"/></svg>As well as architects</li>
    <li><svg viewBox="0 0 14 14"><circle cx="7" cy="7" r="7" fill="#1f3fa8"/><path d="M3.8 7.2l2.2 2.1 4.2-4.4" stroke="#fff" stroke-width="1.6" fill="none"/></svg>Engineers</li>
    <li><svg viewBox="0 0 14 14"><circle cx="7" cy="7" r="7" fill="#1f3fa8"/><path d="M3.8 7.2l2.2 2.1 4.2-4.4" stroke="#fff" stroke-width="1.6" fill="none"/></svg>Contractors to collaboratively present and discuss issues and ideas related to sustainability</li>
    <li><svg viewBox="0 0 14 14"><circle cx="7" cy="7" r="7" fill="#1f3fa8"/><path d="M3.8 7.2l2.2 2.1 4.2-4.4" stroke="#fff" stroke-width="1.6" fill="none"/></svg>With a Texas focus</li>
  </ul>
  <div class="abs divider-v list-div"></div>

  <aside class="abs catalyst">
    <div class="catalyst-head">
      <span class="catalyst-dot"></span>
      <p class="catalyst-title"><span>CATALYST EVENT</span> FOR PUBLIC</p>
    </div>
    <p class="catalyst-body">This event will be a catalyst for public and private project owners to holistically gather information and momentum as we bring the resources and vision needed to achieve the goal of zero carbon emissions from the built environment by 2040, and address water, green space and the natural environment, transportation, equity, and funding, among other topics</p>
  </aside>

  <p class="abs contact phone"><svg viewBox="0 0 12 12"><path d="M2.5 1l2 2-1 1.5c.7 1.5 1.8 2.6 3.3 3.3l1.5-1 2 2-1.3 1.7C5 10 2 7 .8 2.3z" fill="#8cc63f"/></svg>(555) 014-2290</p>
  <p class="abs contact email"><svg viewBox="0 0 12 12"><rect x="1" y="2.5" width="10" height="7" fill="#8cc63f"/><path d="M1 2.5l5 4 5-4" stroke="#fff" stroke-width="1" fill="none"/></svg>dana.reyes@q-vardt.org</p>
  <p class="abs web">www.<span>q-vardt.eventhub</span>.org</p>
</main>
</body>
</html>
```